Kesso Tea Premium Matcha brand Label

This is a label design project for a luxury tea brand. Feel free to be creative within the guidelines.
Attached to this project is a document called “Private Label Design Requirements” with the design guidelines and template. There is another document called "Kesso Tea Packaging Instructions" this has more details necessary to stick to the guidelines in the first document.

I have also attached the certifications to be included as well as different variations of the logo for you to use.

If you have any questions, I am here.
Updates

Need extra days to review

Target Market(s)

Young, active, fun, enjoy the finer things

```html
<!DOCTYPE html>
<html lang="en">
<head>
<meta charset="utf-8">
<title>Kesso Tea – Premium Organic Ceremonial Matcha Label</title>
<link rel="stylesheet" href="https://fonts.googleapis.com/css2?family=Josefin+Sans:wght@600;700&family=Montserrat:wght@500;600;700&display=swap">
<style>
  :root {
    --backdrop: #939497;
    --label-white: #f4f4f4;
    --label-shade: #e2e2e3;
    --matcha-dark: #3f7434;
    --matcha: #4f8a3f;
    --matcha-light: #6aa355;
    --ink: #161616;
    --rim-grey: #b9babc;
    --heading-green: #5a9a3f;
  }
  * { margin: 0; padding: 0; box-sizing: border-box; }
  html, body { width: 1200px; height: 430px; overflow: hidden; }
  body {
    background: var(--backdrop);
    font-family: "Montserrat", Arial, sans-serif;
    color: var(--ink);
    position: relative;
  }
  .label {
    position: absolute;
    left: 30px; top: 70px;
    width: 1140px; height: 290px;
  }
  .label-art { position: absolute; inset: 0; }
  .panel { position: absolute; top: 0; height: 290px; }
  .panel-origin { left: 0; width: 380px; }
  .panel-front { left: 380px; width: 380px; text-align: center; }
  .panel-details { left: 760px; width: 380px; }

  .origin-text {
    position: absolute; left: 70px; top: 150px;
    font-size: 11.5px; font-weight: 600; line-height: 1.35;
  }
  .origin-text .certifier { margin-top: 8px; }

  .brand {
    position: absolute; left: 0; right: 0; top: 58px;
    display: flex; flex-direction: column; align-items: center; gap: 6px;
  }
  .brand-mark {
    width: 34px; height: 34px; border-radius: 50%;
    background: var(--ink);
  }
  .brand-name {
    font-family: "Josefin Sans", Arial, sans-serif;
    font-weight: 700; font-size: 13px; color: var(--ink);
  }
  .product-title {
    position: absolute; left: 0; right: 0; top: 134px;
    font-family: "Josefin Sans", Arial, sans-serif;
    font-weight: 700; font-size: 30px; line-height: 1.05;
    letter-spacing: 0.3px; color: var(--ink);
  }
  .net-weight {
    position: absolute; left: 0; right: 0; top: 258px;
    font-family: "Josefin Sans", Arial, sans-serif;
    font-weight: 600; font-size: 11px; color: #e8e8e8;
    letter-spacing: 0.5px;
  }

  .details-text { position: absolute; left: 60px; top: 62px; width: 300px; }
  .details-text h3 {
    font-size: 12px; font-weight: 700; color: var(--heading-green);
    line-height: 1.2;
  }
  .details-text p, .details-text li {
    font-size: 8.5px; font-weight: 600; line-height: 1.4;
  }
  .details-text ul { list-style: none; margin-bottom: 6px; }
  .details-text li::before { content: "• "; }
  .details-text .ingredients { margin-bottom: 4px; }
  .cert-row { display: flex; align-items: center; gap: 6px; margin-top: 6px; }
  .cert-square { width: 22px; height: 22px; background: var(--matcha); border-radius: 2px; }
  .cert-circle { width: 22px; height: 22px; border-radius: 50%; border: 2px solid var(--matcha-dark); background: var(--label-white); }
  .storage-note {
    margin-left: 8px; font-size: 8.5px; font-weight: 700;
    line-height: 1.3; text-transform: uppercase;
  }
</style>
</head>
<body>
  <section class="label" aria-label="Unwrapped matcha jar label">
    <svg class="label-art" width="1140" height="290" viewBox="0 0 1140 290" aria-hidden="true">
      <defs>
        <linearGradient id="labelWhite" x1="0" y1="0" x2="0" y2="1">
          <stop offset="0" stop-color="#f6f6f6"/>
          <stop offset="1" stop-color="#e4e4e5"/>
        </linearGradient>
        <linearGradient id="matchaFill" x1="0" y1="0" x2="1" y2="0">
          <stop offset="0" stop-color="#3f7434"/>
          <stop offset="0.6" stop-color="#4f8a3f"/>
          <stop offset="1" stop-color="#6aa355"/>
        </linearGradient>
        <linearGradient id="wedgeFill" x1="0" y1="0" x2="1" y2="0">
          <stop offset="0" stop-color="#4f8a3f"/>
          <stop offset="1" stop-color="#7ab264"/>
        </linearGradient>
      </defs>
      <rect class="label-base" width="1140" height="290" fill="url(#labelWhite)"/>

      <!-- origin panel edge wedge -->
      <polygon points="322,0 380,0 380,180" fill="url(#wedgeFill)"/>
      <line x1="322" y1="0" x2="380" y2="180" stroke="var(--ink)" stroke-width="3"/>

      <!-- front panel -->
      <path d="M380 0 H760 V130 Q760 282 570 290 Q380 282 380 130 Z" fill="var(--ink)"/>
      <path d="M380 0 H760 V122 Q760 272 570 280 Q380 272 380 122 Z" fill="var(--rim-grey)"/>
      <path d="M380 0 H760 V116 Q760 262 570 272 Q380 262 380 116 Z" fill="url(#matchaFill)"/>
      <path d="M482 262 Q570 236 658 262 Q570 288 482 262 Z" fill="var(--ink)"/>

      <!-- details panel edge wedge -->
      <polygon points="760,0 815,0 760,180" fill="url(#wedgeFill)"/>
      <line x1="815" y1="0" x2="760" y2="180" stroke="var(--ink)" stroke-width="3"/>
    </svg>

    <div class="panel panel-origin">
      <div class="origin-text">
        <p>Product of Japan</p>
        <p>Distributed by:</p>
        <p>Kesso Tea Co. | Brookhaven, Ga</p>
        <p class="certifier">Certified Organic by Verdant Cert</p>
      </div>
    </div>

    <div class="panel panel-front">
      <div class="brand">
        <span class="brand-mark"></span>
        <span class="brand-name">Kesso Tea</span>
      </div>
      <h1 class="product-title">PREMIUM ORGANIC<br>CEREMONIAL MATCHA</h1>
      <p class="net-weight">Net Wt: 30g</p>
    </div>

    <div class="panel panel-details">
      <div class="details-text">
        <h3>Ingredients:</h3>
        <p class="ingredients">Premium Organic Japanese Matcha Green Tea</p>
        <h3>Instructions:</h3>
        <ul>
          <li>2 tsp of Matcha</li>
          <li>2oz of Water (170-180 degrees F)</li>
          <li>Whisk in a W formation until frothy</li>
          <li>Sweeten to taste</li>
        </ul>
        <div class="cert-row">
          <span class="cert-square" role="img" aria-label="Non-GMO certification badge"></span>
          <span class="cert-circle" role="img" aria-label="Organic certification badge"></span>
          <p class="storage-note">Keep refrigerated<br>for quality</p>
        </div>
      </div>
    </div>
  </section>
</body>
</html>
```